MBRDC redesign and update stationary bc envelopes.

Stationary, Envelopes, Brochures, Business Card. Need to add second surgeon and two other offices. I need everything to match. I am a oral & maxillofacial surgeon.
Additional surgeon and three office addresses.
Jae Min Park, DMD, MD, INC

3718 Silver Meadow Parkway
Cedar Knoll, CA 90417

642 Lorin Way, Suite 101
Willow Bend, CA. 90428

2317 Vale Street, Suite 105
Granite Falls, CA. 90439
Updates

Logo design uploaded. Zapfino Extra/Adobe Garamond/Palatino are fonts used before. Not sure what is on exisiting stationary.

Target Market(s)

Referral dentist and sometimes patients. I am a oral & Maxillofacial surgeon.

Industry/Entity Type

Dental Clinic

Font styles to use
Serif
Script

Requirements
Must have
• Color of existing stationary. Update is possible.
Nice to have
• Conservative/modern
Should not have
• Playful

```html
<!DOCTYPE html>
<html lang="en">
<head>
<meta charset="utf-8">
<title>MBRDC Business Cards</title>
<link rel="stylesheet" href="https://fonts.googleapis.com/css2?family=EB+Garamond:wght@400;500;600&family=Lato:wght@400&display=swap">
<style>
  :root {
    --bg: #ebe9e6;
    --card: #fbfbfa;
    --brown: #5a3e2e;
    --green: #5e8a1e;
    --text: #3b2a20;
  }
  * { margin: 0; padding: 0; box-sizing: border-box; }
  html, body { width: 1200px; height: 960px; overflow: hidden; background: var(--bg); }
  body { position: relative; font-family: "EB Garamond", Georgia, serif; color: var(--text); }

  .card {
    position: absolute; left: 220px; width: 760px; height: 434px;
    background: var(--card);
    box-shadow: 0 2px 10px rgba(0,0,0,.12);
    overflow: hidden;
  }
  .card--front { top: 26px; }
  .card--back { top: 500px; }

  .brand { text-align: center; }
  .brand__name { font-size: 54px; font-weight: 500; color: var(--brown); letter-spacing: 2px; line-height: 1; }
  .brand--front { position: absolute; top: 70px; left: 0; right: 0; }

  .services { position: absolute; top: 170px; left: 0; right: 0; text-align: center; font-size: 21px; line-height: 1.45; }
  .services span::before { content: "•"; color: var(--green); margin: 0 6px 0 10px; }

  .rule { position: absolute; left: 0; right: 0; top: 332px; height: 2px; background: var(--green); }
  .band {
    position: absolute; left: 0; right: 0; bottom: 0; height: 92px;
    background: var(--brown); color: #f3eee9;
    display: flex; align-items: center; justify-content: center;
    font-size: 30px; letter-spacing: .5px;
  }

  .doctor { position: absolute; left: 52px; top: 56px; }
  .doctor__name { font-size: 34px; font-weight: 600; color: var(--brown); }
  .doctor__board { display: flex; align-items: center; gap: 10px; margin-top: 6px; }
  .seal { width: 36px; height: 36px; border-radius: 50%; border: 2px solid #9aaa86; background: #eef1e8; flex: none; }
  .doctor__cred { font-family: "Lato", Arial, sans-serif; color: var(--green); font-size: 17px; line-height: 1.2; }

  .brand--back { position: absolute; right: 52px; top: 60px; text-align: right; }
  .brand--back .brand__name { font-size: 44px; }

  .main-office { position: absolute; left: 52px; top: 212px; font-size: 21px; line-height: 1.3; }
  .contacts { list-style: none; margin-top: 10px; }
  .contacts li { display: flex; align-items: center; gap: 10px; }
  .contacts svg { width: 16px; height: 16px; fill: var(--green); flex: none; }

  .branches { position: absolute; right: 52px; top: 190px; text-align: right; font-size: 21px; line-height: 1.3; }
  .branches p + p { margin-top: 8px; }
</style>
</head>
<body>

<section class="card card--front">
  <div class="brand brand--front"><span class="brand__name">MBRDC</span></div>
  <div class="services">
    <div><span>Dentoalveolar Surgery</span><span>Dental Implant Surgery</span><span>Orthognathic Surgery</span></div>
    <div><span>Facial Trauma Surgery</span><span>Preprosthetic and Reconstructive Surgery</span></div>
    <div><span>TMJ Disorders and Surgery</span><span>Obstructive Sleep Apnea Surgery</span></div>
  </div>
  <div class="rule"></div>
  <div class="band">www.mbrdcsurgery.com</div>
</section>

<section class="card card--back">
  <div class="doctor">
    <h1 class="doctor__name">Jae Min Park, DMD, MD, INC</h1>
    <div class="doctor__board">
      <span class="seal" role="img" aria-label="Certification seal"></span>
      <p class="doctor__cred">Diplomate of the Allied Council of<br>Oral &amp; Facial Surgery</p>
    </div>
  </div>

  <div class="brand brand--back"><span class="brand__name">MBRDC</span></div>

  <div class="main-office">
    <p>3718 Silver Meadow Parkway<br>Cedar Knoll, CA 90417</p>
    <ul class="contacts">
      <li><svg viewBox="0 0 16 16"><path d="M3 1h3l1 4-2 1a9 9 0 0 0 5 5l1-2 4 1v3c0 1-1 2-2 2A13 13 0 0 1 1 3c0-1 1-2 2-2z"/></svg>916.555.0142</li>
      <li><svg viewBox="0 0 16 16"><path d="M4 1h8v4H4zM1 6h14v7h-3v2H4v-2H1zM5 10v4h6v-4z"/></svg>916.555.0187</li>
      <li><svg viewBox="0 0 16 16"><path d="M1 3h14v10H1zM2 4l6 5 6-5v1l-6 5-6-5z" fill-rule="evenodd"/></svg>drpark@mbrdcsurgery.com</li>
      <li><svg viewBox="0 0 16 16"><circle cx="8" cy="8" r="7"/></svg>www.mbrdcsurgery.com</li>
    </ul>
  </div>

  <div class="branches">
    <p>642 Lorin Way, Suite 101<br>Willow Bend, CA. 90428</p>
    <p>2317 Vale Street, Suite 105<br>Granite Falls, CA. 90439</p>
  </div>
</section>

</body>
</html>
```